Eye Catching Email Marketing design

Our health care consulting firm is based in New York City. We sell health care consulting Services to medical practices (doctors). We need a powerful email marketing design to use as one of our primary selling tools to attract new clients. The Design should convey health care knowledge, expertise professionalism, cutting edge technology and the services we offer. <br/>The design should incorporate our logo and its colors (blue and white) but we want it to be eye catching and vibrant, so other colors be included. We are open to the designer's creativity. Any pictures used should show diversity (races)and should include women. Designers can find our logo and other graphics on our website at www harbor ridge advisory.com. Please feel free to ask questions.<br/><br/>

Target Market(s)

Health care professionals, executives and Doctors.

Colors

Designer to choose colors to be used in the design.

Requirements
Nice to have
• What ever the design feels will help make this design vibrant

```html
<!DOCTYPE html>
<html lang="en">
<head>
<meta charset="utf-8">
<title>Harbor Ridge Advisory – Email</title>
<link href="https://fonts.googleapis.com/css2?family=Mulish:wght@400;700;800&family=Questrial&display=swap" rel="stylesheet">
<style>
  :root{
    --navy:#0f4ea0;
    --sky:#2fa3d6;
    --deep:#17378f;
    --ink:#1e1e1e;
    --grey:#8a8a8a;
    --rule:#bdbdbd;
    --white:#ffffff;
  }
  *{margin:0;padding:0;box-sizing:border-box}
  html,body{width:1200px;height:4576px;overflow:hidden;background:var(--white)}
  body{position:relative;font-family:"Mulish",sans-serif;color:var(--ink)}
  .abs{position:absolute}
  .hero{left:0;top:0;width:1200px;height:952px;background:linear-gradient(160deg,#e9eef2 0%,#c9d4dc 45%,#8fa0ad 100%)}
  .brand{left:40px;top:150px;display:flex;align-items:center;gap:18px;font-weight:700;font-size:32px;color:var(--navy);letter-spacing:1px}
  .brand-dot{width:40px;height:40px;border-radius:50%;background:var(--navy)}
  .tagline{left:0;top:952px;width:1200px;height:250px;background:var(--sky)}
  .tagline .rule{position:absolute;left:40px;width:1120px;height:3px;background:var(--white)}
  .tagline h1{position:absolute;left:0;width:1200px;top:1044px;top:92px;text-align:center;color:var(--white);font-size:50px;font-weight:700}
  .services-title{left:0;top:1258px;width:1200px;text-align:center;font-size:60px;font-weight:800}
  .services-title .light{color:var(--sky)} .services-title .dark{color:var(--navy)}
  .card{width:522px;height:162px;background:var(--white);box-shadow:2px 3px 6px rgba(0,0,0,.18);display:flex}
  .card .num{width:148px;height:100%;display:flex;align-items:center;justify-content:center;color:var(--white);font-size:58px;font-weight:800}
  .card .num.dark{background:var(--navy)} .card .num.light{background:var(--sky)}
  .card .label{padding-left:20px;display:flex;align-items:center;font-size:37px;line-height:1.4;font-weight:700;color:#2a2a2a}
  .help{left:0;top:1910px;width:654px;height:646px;background:linear-gradient(160deg,#1a3a8e,#12328a 60%,#1d3d9e)}
  .help h2{position:absolute;left:38px;top:96px;font-size:60px;font-weight:800;color:var(--white)}
  .help ul{position:absolute;left:40px;top:252px;list-style:none;color:var(--white);font-size:35px}
  .help li{height:72px}
  .help li::before{content:"\2022";margin-right:12px}
  .help-photo{left:654px;top:1910px;width:546px;height:646px;background:linear-gradient(180deg,#5b4235 0%,#a67e68 35%,#e9e3e2 70%,#f4f0ef 100%)}
  .expertise{left:0;top:2560px;width:1200px;height:644px;background:linear-gradient(135deg,#3e4a57,#56626e 50%,#3a4450)}
  .expertise h2{position:absolute;left:0;width:1200px;top:92px;text-align:center;color:var(--white);font-size:56px;font-weight:800;line-height:70px}
  .expertise p{position:absolute;left:260px;width:680px;top:254px;text-align:center;color:#f2f2f2;font-size:32px;line-height:56px}
  .contact-title{left:0;top:3300px;width:1200px;text-align:center;font-family:"Questrial",sans-serif;font-size:82px;color:#111}
  .accent{left:564px;top:3442px;width:72px;height:7px;background:var(--sky)}
  .contact-sub{left:0;top:3484px;width:1200px;text-align:center;font-family:"Questrial",sans-serif;font-size:50px;color:#1f6cb5}
  .icon{width:156px;height:156px;left:522px;border-radius:50%;background:var(--navy);display:flex;align-items:center;justify-content:center}
  .c-label{left:0;width:1200px;text-align:center;font-size:31px;color:var(--grey)}
  .c-value{left:0;width:1200px;text-align:center;font-size:34px;font-weight:700;color:#111}
  .subscribe{left:450px;top:4268px;width:300px;height:96px;background:var(--navy);color:var(--white);font-size:33px;font-weight:800;display:flex;align-items:center;justify-content:center}
  .footer-rule{left:40px;top:4418px;width:1120px;height:2px;background:#555}
  .social{left:562px;top:4424px;width:76px;height:76px;border-radius:50%;background:var(--navy)}
  .copyright{left:0;top:4514px;width:1200px;text-align:center;font-size:28px;color:#222}
</style>
</head>
<body>
  <div class="abs hero" role="img" aria-label="Photo of a diverse team of doctors meeting around a conference table"></div>
  <div class="abs brand"><span class="brand-dot"></span>HARBOR RIDGE ADVISORY LLC</div>

  <section class="abs tagline">
    <div class="rule" style="top:42px"></div>
    <h1>Advancing Healthcare Operations</h1>
    <div class="rule" style="top:222px"></div>
  </section>

  <h2 class="abs services-title"><span class="light">OUR</span> <span class="dark">SERVICES</span></h2>
  <div class="abs card" style="left:48px;top:1410px"><div class="num dark">01</div><div class="label">REVENUE CYCLE<br>MANAGEMENT</div></div>
  <div class="abs card" style="left:622px;top:1410px"><div class="num light">03</div><div class="label">HEALTHCARE<br>INNOVATION</div></div>
  <div class="abs card" style="left:48px;top:1616px"><div class="num light">02</div><div class="label">COMPLIANCE<br>MANAGEMENT</div></div>
  <div class="abs card" style="left:622px;top:1616px"><div class="num dark">04</div><div class="label">PRACTICE<br>MANAGEMENT</div></div>

  <section class="abs help">
    <h2>WE CAN HELP YOU</h2>
    <ul>
      <li>INCREASE MARGINS</li>
      <li>INTEGRATE NEW TECHNOLOGY</li>
      <li>TRANSFORM OPERATIONS</li>
      <li>SAFEGUARD YOUR PRACTICE</li>
    </ul>
  </section>
  <div class="abs help-photo" role="img" aria-label="Photo of a smiling female doctor in a white coat with a stethoscope"></div>

  <section class="abs expertise" role="img" aria-label="Darkened photo of medical staff in discussion">
    <h2>Expertise Your Medical<br>Practice Deserves</h2>
    <p>“The expertise of our team encompasses full spectrum knowledge in revenue cycle management, practice management, regulatory compliance, and healthcare innovation.”</p>
  </section>

  <h2 class="abs contact-title">Have Questions?</h2>
  <div class="abs accent"></div>
  <p class="abs contact-sub">Talk to a Member of Our Team</p>

  <div class="abs icon" style="top:3596px">
    <svg width="40" height="40" viewBox="0 0 24 24"><path fill="#fff" d="M6.6 10.8a15.1 15.1 0 0 0 6.6 6.6l2.2-2.2c.3-.3.7-.4 1-.2 1.1.4 2.3.6 3.6.6.6 0 1 .4 1 1V20c0 .6-.4 1-1 1C10.6 21 3 13.4 3 4c0-.6.4-1 1-1h3.5c.6 0 1 .4 1 1 0 1.3.2 2.5.6 3.6.1.3 0 .7-.2 1z"/></svg>
  </div>
  <p class="abs c-label" style="top:3768px">Phone :</p>
  <p class="abs c-value" style="top:3830px">(555) 214-0187</p>

  <div class="abs icon" style="top:3928px">
    <svg width="50" height="40" viewBox="0 0 30 22"><path fill="#fff" d="M0 2l15 10L30 2V0H0z"/><path fill="#fff" d="M0 5v17h30V5L15 15z"/></svg>
  </div>
  <p class="abs c-label" style="top:4100px">Email :</p>
  <p class="abs c-value" style="top:4162px">info@harborridgeadvisory.com</p>

  <div class="abs subscribe">Subscribe</div>
  <div class="abs footer-rule"></div>
  <div class="abs social"></div>
  <p class="abs copyright">Copyrights @ 2020 Harbor Ridge Advisory.</p>
</body>
</html>
```